Design a large parking banner – mandatory ticket validation in the shop

Banner Size:
548 cm (width) x 154 cm (height)
Note: The banner will be placed in a metal frame at our parking lot entrance, fully visible to every incoming truck driver. The message must be easy to read from a distance.
Goal of the Banner:
To inform all truck drivers that they must validate their entry ticket inside the shop, even if they are parking for a short time.
The message must be displayed in multiple languages for international drivers.
Mandatory Content:
Main message – in multiple languages (clearly separated or stacked):
Dutch (NL): Vergeet je ticket niet te valideren in de shop – verplicht, ook bij kort parkeren!
French (FR): N'oubliez pas de valider votre ticket à la boutique – obligatoire, même pour un court arrêt !
English (EN): Don't forget to validate your entry ticket in the shop – mandatory, even for short stops!
German (DE): Vergessen Sie nicht, Ihr Einfahrticket im Shop zu entwerten – Pflicht, auch bei kurzem Parken!
Polish (PL): Nie zapomnij zatwierdzić biletu w sklepie – obowiązkowe, nawet przy krótkim postoju!
Romanian (RO): Nu uitați să validați biletul în magazin – obligatoriu, chiar și pentru opriri scurte!
You can include more languages if space allows, but these are essential.
Opening Hours Block (in one section below):
Shop Opening Hours
Mon – Fri: 05:30 – 22:00
Sat & Sun: 08:00 – 22:00
Style & Branding:
The design must match the visual identity of Haulport 41Ter
Please refer to the attached photos of existing parking signage for guidance on colors, typography, and layout style
Our logo (attached) must be clearly visible and professionally integrated
Feel free to use icons or pictograms to visually support the message (e.g., ticket, truck, arrow)
Readability is key – large, bold text and high contrast colors that are visible from a distance
Target Audience:
International truck drivers – people who need fast, clear communication. Not everyone speaks the local language, so visual clarity and multilingual messaging are critical.
File Requirements:
Print-ready file (PDF or EPS) – 300 dpi at 1:10 scale
Include 5 cm bleed on all sides
Provide open source files if possible (AI or PSD)

```html
<!DOCTYPE html>
<html lang="en">
<head>
<meta charset="utf-8">
<title>Haulport 41Ter – Parking Ticket Validation Banner</title>
<link href="https://fonts.googleapis.com/css2?family=Roboto+Condensed:wght@400;700&display=swap" rel="stylesheet">
<style>
  :root {
    --navy: #1d2047;
    --red: #d3141c;
    --blue: #1f7cc6;
    --white: #ffffff;
    --ink: #111111;
    --backdrop: #e8ecf0;
  }
  * { box-sizing: border-box; margin: 0; padding: 0; }
  html, body {
    width: 1200px; height: 1045px; overflow: hidden;
    background: var(--backdrop);
    font-family: "Roboto Condensed", "Arial Narrow", sans-serif;
  }
  .banner {
    position: absolute; left: 40px; top: 365px;
    width: 1120px; height: 315px;
    background: var(--navy); color: var(--white);
    overflow: hidden;
  }
  .brand {
    position: absolute; left: 28px; top: 24px;
    display: flex; align-items: center; gap: 8px;
  }
  .brand-mark { width: 16px; height: 16px; background: var(--blue); }
  .brand-name { font-weight: 700; font-size: 27px; letter-spacing: -0.5px; color: var(--white); }
  .headline {
    position: absolute; left: 222px; top: 26px;
    font-weight: 700; font-size: 28px; letter-spacing: -0.2px; white-space: nowrap;
  }
  .rule { position: absolute; left: 0; top: 72px; width: 100%; height: 3px; background: var(--red); }
  .must-read {
    position: absolute; left: 28px; top: 86px;
    display: flex; align-items: center; gap: 8px;
    font-weight: 700; font-size: 26px;
  }
  .must-read svg { width: 28px; height: 28px; }
  .languages { position: absolute; left: 40px; top: 126px; list-style: none; }
  .languages li {
    display: flex; align-items: center; gap: 12px;
    font-weight: 700; font-size: 16.5px; height: 29px; white-space: nowrap;
  }
  .languages svg { width: 18px; height: 12px; flex: none; }
  .info { position: absolute; left: 880px; top: 96px; width: 220px; text-align: center; }
  .parking-sign { display: block; margin: 0 auto; width: 56px; height: 86px; }
  .parking-arrow {
    display: inline-block; margin-top: -2px;
    background: var(--white); color: var(--ink);
    font-size: 18px; padding: 3px 10px; letter-spacing: 0.3px;
  }
  .hours-title {
    margin-top: 8px; background: var(--blue); border-radius: 4px;
    font-weight: 700; font-size: 19px; padding: 3px 0;
  }
  .hours { list-style: none; margin: 8px auto 0; width: 170px; }
  .hours li {
    font-weight: 700; font-size: 14px; padding: 2px 0 3px;
    border-bottom: 2px solid var(--red); margin-bottom: 8px;
  }
</style>
</head>
<body>
  <main class="banner">
    <div class="brand">
      <span class="brand-mark"></span>
      <span class="brand-name">Haulport 41Ter</span>
    </div>
    <h1 class="headline">"Attention Drivers: Entry Tickets Must Be Verified Inside the Shop."</h1>
    <div class="rule"></div>

    <div class="must-read">
      <svg viewBox="0 0 28 28" aria-hidden="true">
        <circle cx="14" cy="14" r="12" fill="none" stroke="var(--red)" stroke-width="2.5"/>
        <rect x="12.5" y="6" width="3" height="11" fill="var(--white)"/>
        <rect x="12.5" y="19.5" width="3" height="3" fill="var(--white)"/>
      </svg>
      <span>MUST READ!</span>
    </div>

    <ul class="languages">
      <li><svg viewBox="0 0 18 12" aria-hidden="true"><path d="M1 1l5 5-5 5M9 1l5 5-5 5" fill="none" stroke="var(--red)" stroke-width="2"/></svg>English (EN): Don't forget to validate your entry ticket in the shop – mandatory, even for short stops!</li>
      <li><svg viewBox="0 0 18 12" aria-hidden="true"><path d="M1 1l5 5-5 5M9 1l5 5-5 5" fill="none" stroke="var(--red)" stroke-width="2"/></svg>French (FR): N'oubliez pas de valider votre ticket à la boutique – obligatoire, même pour un court arrêt !</li>
      <li><svg viewBox="0 0 18 12" aria-hidden="true"><path d="M1 1l5 5-5 5M9 1l5 5-5 5" fill="none" stroke="var(--red)" stroke-width="2"/></svg>Dutch (NL): Vergeet je ticket niet te valideren in de shop – verplicht, ook bij kort parkeren!</li>
      <li><svg viewBox="0 0 18 12" aria-hidden="true"><path d="M1 1l5 5-5 5M9 1l5 5-5 5" fill="none" stroke="var(--red)" stroke-width="2"/></svg>German (DE): Vergessen Sie nicht, Ihr Einfahrticket im Shop zu entwerten – Pflicht, auch bei kurzem Parken!</li>
      <li><svg viewBox="0 0 18 12" aria-hidden="true"><path d="M1 1l5 5-5 5M9 1l5 5-5 5" fill="none" stroke="var(--red)" stroke-width="2"/></svg>Polish (PL): Nie zapomnij zatwierdzić biletu w sklepie – obowiązkowe, nawet przy krótkim postoju!</li>
      <li><svg viewBox="0 0 18 12" aria-hidden="true"><path d="M1 1l5 5-5 5M9 1l5 5-5 5" fill="none" stroke="var(--red)" stroke-width="2"/></svg>Romanian (RO): Nu uitați să validați biletul în magazin – obligatoriu, chiar și pentru opriri scurte!</li>
    </ul>

    <aside class="info">
      <svg class="parking-sign" viewBox="0 0 56 86" aria-label="Parking sign">
        <rect x="1.5" y="1.5" width="53" height="70" rx="9" fill="var(--blue)" stroke="var(--white)" stroke-width="3"/>
        <text x="28" y="56" text-anchor="middle" font-family="Roboto Condensed, sans-serif" font-weight="700" font-size="52" fill="var(--white)">P</text>
        <rect x="23" y="72" width="10" height="14" fill="var(--white)"/>
      </svg>
      <div class="parking-arrow">← PARKING →</div>
      <div class="hours-title">SHOP OPENING HOURS</div>
      <ul class="hours">
        <li>MON – FRI: 05:30 – 22:00</li>
        <li>SAT &amp; SUN: 08:00 – 22:00</li>
      </ul>
    </aside>
  </main>
</body>
</html>
```